Business Card Design

We need the business card for our new business based in St. Marys, we manufacture mainly bubble wraps. And we would like the design to use our company logo and also make it easy for people to understand right away we are bubble wrap manufacturer

Industry/Entity Type

Business

Contact Information for Business Card

Cushtane Pty Ltd, 14 Larkin Road St. Marys NSW 2760, Tel: 02 9471 5826, Fax: 9471 5839, Dara Oyelaran, General Manager, Mobile :0438 217 564, dara.oyelaran@cushtane.com.au, Website: cushtane.com.au

```html
<!DOCTYPE html>
<html lang="en">
<head>
<meta charset="utf-8">
<title>Cushtane Pty Ltd – Business Card</title>
<link href="https://fonts.googleapis.com/css2?family=Open+Sans:wght@400;600;800&display=swap" rel="stylesheet">
<style>
  :root {
    --bg: #e9e7e3;
    --card: #ffffff;
    --card-shade: #f1f1f1;
    --ink-grey: #77787b;
    --ink-light: #8e9093;
    --brand-red: #d3202f;
    --shadow: rgba(0,0,0,0.18);
  }
  * { box-sizing: border-box; margin: 0; padding: 0; }
  html, body { width: 1200px; height: 885px; overflow: hidden; }
  body {
    background: var(--bg);
    font-family: "Open Sans", Arial, sans-serif;
    position: relative;
  }
  .card {
    position: absolute;
    width: 640px;
    height: 366px;
    border-radius: 18px;
    background: linear-gradient(135deg, var(--card) 40%, var(--card-shade));
    box-shadow: 0 10px 28px var(--shadow);
    overflow: hidden;
  }
  .card--front { left: 70px; top: 70px; }
  .card--back { left: 490px; top: 470px; }

  .wordmark {
    font-weight: 800;
    color: var(--ink-grey);
    letter-spacing: -1px;
    line-height: 1;
    display: flex;
    align-items: center;
    gap: 12px;
  }
  .wordmark__square {
    width: 0.55em; height: 0.55em;
    background: var(--brand-red);
  }
  .tagline {
    color: var(--ink-light);
    font-size: 13px;
    letter-spacing: 5px;
    text-transform: uppercase;
    margin-top: 10px;
  }

  /* Front */
  .front__brand { position: absolute; left: 44px; top: 66px; }
  .front__brand .wordmark { font-size: 60px; }
  .front__person { position: absolute; right: 44px; top: 52px; text-align: right; }
  .person__name { color: var(--brand-red); font-size: 24px; font-weight: 400; }
  .person__title { color: var(--ink-grey); font-size: 16px; font-weight: 600; margin-top: 2px; }
  .front__rule {
    position: absolute; left: 44px; right: 44px; top: 196px; height: 1.5px;
    background: linear-gradient(90deg, transparent, var(--brand-red) 15%, var(--brand-red) 85%, transparent);
  }
  .front__contacts { position: absolute; left: 44px; top: 220px; list-style: none; }
  .contact {
    display: flex; align-items: center; gap: 12px;
    color: var(--ink-grey); font-size: 18px; line-height: 28px;
  }
  .contact__icon { width: 20px; height: 20px; flex: none; }
  .front__address {
    position: absolute; right: 44px; bottom: 40px; text-align: right;
    color: var(--ink-grey); font-size: 16px; line-height: 22px;
  }

  /* Back */
  .back__brand { position: absolute; left: 0; right: 0; top: 118px; text-align: center; }
  .back__brand .wordmark { font-size: 72px; justify-content: center; }
  .back__site {
    position: absolute; left: 0; right: 0; top: 70px;
    display: flex; align-items: center; justify-content: center; gap: 16px;
    color: var(--brand-red); font-size: 20px; font-weight: 600;
  }
  .back__site-rule { width: 90px; height: 1.5px; background: var(--brand-red); }
</style>
</head>
<body>

<section class="card card--front" aria-label="Business card front">
  <div class="front__brand">
    <div class="wordmark">CUSHTANE<span class="wordmark__square"></span></div>
    <div class="tagline">Protective Packaging Solutions</div>
  </div>

  <div class="front__person">
    <div class="person__name">Dara Oyelaran</div>
    <div class="person__title">General Manager</div>
  </div>

  <div class="front__rule"></div>

  <ul class="front__contacts">
    <li class="contact">
      <svg class="contact__icon" viewBox="0 0 20 20" aria-label="Telephone"><rect width="20" height="20" rx="2" fill="var(--brand-red)"/><path d="M5 6c0 5 4 9 9 9l1.5-2-2.5-1.5-1.2 1.2c-1.6-.7-2.8-1.9-3.5-3.5L9.5 8 8 5.5z" fill="#fff"/></svg>
      02 9471 5826
    </li>
    <li class="contact">
      <svg class="contact__icon" viewBox="0 0 20 20" aria-label="Mobile"><rect width="20" height="20" rx="2" fill="var(--brand-red)"/><rect x="6.5" y="3.5" width="7" height="13" rx="1" fill="none" stroke="#fff" stroke-width="1.4"/><circle cx="10" cy="14" r=".9" fill="#fff"/></svg>
      0438 217 564
    </li>
    <li class="contact">
      <svg class="contact__icon" viewBox="0 0 20 20" aria-label="Fax"><rect width="20" height="20" rx="2" fill="var(--brand-red)"/><rect x="4" y="8" width="12" height="7" fill="none" stroke="#fff" stroke-width="1.4"/><rect x="6.5" y="4" width="7" height="4" fill="#fff"/></svg>
      9471 5839
    </li>
    <li class="contact">
      <svg class="contact__icon" viewBox="0 0 20 20" aria-label="Email"><rect width="20" height="20" rx="2" fill="var(--brand-red)"/><rect x="4" y="6" width="12" height="8" fill="none" stroke="#fff" stroke-width="1.4"/><path d="M4 6l6 5 6-5" fill="none" stroke="#fff" stroke-width="1.4"/></svg>
      dara.oyelaran@cushtane.com.au
    </li>
  </ul>

  <address class="front__address" style="font-style:normal">
    14 Larkin Road St.<br>Marys NSW 2760
  </address>
</section>

<section class="card card--back" aria-label="Business card back">
  <div class="back__site">
    <span class="back__site-rule"></span>
    cushtane.com.au
    <span class="back__site-rule"></span>
  </div>
  <div class="back__brand">
    <div class="wordmark">CUSHTANE<span class="wordmark__square"></span></div>
    <div class="tagline">Protective Packaging Solutions</div>
  </div>
</section>

</body>
</html>
```